Online interactive tutorial for year 2 to year 12 students in Australia

Website design for a new online tutorial for year 2 to year 12 students in Australia.

- The tutorial will be conducted via live webcam and within a dedicated interactive space
- The tutorial will be provided by high scoring undergraduates studying in top Australian universities.
- The tutors will be going through interviews & assessments & only top students are allowed to apply.
- Parents will do search and select tutor and have short 15 mins video interaction with potential tutors before booking them for their children for tutoring.
- hourly cost of booking (no monthly subscription or no hour limits)
- Tutors will have their own profile

Please see the attached for detailed page functionality.

The look and feel of the design must consider the following:
- must be educational but not dull and should stand out
- must appeal to younger generation - tutees (8-18 years), tutors (19-25), parents (30-50).
- Ideas for Logos (brivora.com.au but not confirmed)

Target Market(s)

tutees (8-18 years), tutors (19-25 years), parents (30-50 years).

Industry/Entity Type

Education

Coding

Coded - Design and coding required

Number of Pages Required

5+ page

Font styles to use
Serif

Requirements
Must have
• The look and feel of the design must consider the following:
• - must be educational but not dull and should stand out
• - must appeal to younger generation - tutees (8-18 years), tutors (19-25), parents (30-50).
Should not have
• Dullness

```html
<!DOCTYPE html>
<html lang="en">
<head>
<meta charset="utf-8">
<title>Brivora Online Tutoring</title>
<link href="https://fonts.googleapis.com/css2?family=Roboto:wght@300;400;500;700&family=Roboto+Condensed:wght@400;700&display=swap" rel="stylesheet">
<style>
:root{
  --blue:#1f8fd6;
  --blue-dark:#1677b8;
  --blue-band:#2a98dc;
  --orange:#f39c1f;
  --green:#8cc63f;
  --ink:#2f3438;
  --text:#6b7177;
  --muted:#9aa0a6;
  --line:#e4e7ea;
  --footer:#1d8bd2;
  --bottom:#2a2d30;
  --training:#2e3d2b;
  --white:#ffffff;
}
*{margin:0;padding:0;box-sizing:border-box}
html,body{width:1200px;height:2940px;overflow:hidden}
body{position:relative;font-family:"Roboto",Arial,sans-serif;color:var(--text);background:var(--white)}
.abs{position:absolute}
h2.section-title{font-family:"Roboto Condensed","Roboto",sans-serif;font-weight:400;font-size:30px;color:var(--ink);text-transform:uppercase;text-align:center;letter-spacing:1px}
h2.section-title::after{content:"";display:block;width:50px;height:2px;background:var(--blue);margin:12px auto 0}
p.small{font-size:13px;line-height:20px}

/* header */
.site-header{left:0;top:0;width:1200px;height:80px;background:var(--white)}
.brand{left:100px;top:20px;font-size:34px;font-weight:700;color:var(--blue);letter-spacing:.5px}
.main-nav{right:100px;top:0;height:80px;display:flex;gap:28px;align-items:center}
.main-nav a{font-size:13px;color:var(--ink);text-decoration:none;font-weight:500;text-transform:uppercase;height:80px;line-height:80px}
.main-nav a.active{color:var(--blue);border-bottom:3px solid var(--blue)}

/* hero */
.hero{left:0;top:80px;width:1200px;height:540px;overflow:hidden}
.hero-photo{position:absolute;inset:0;background:linear-gradient(100deg,#3c2a1e 0%,#6b4a33 30%,#a57c58 55%,#d9c3a8 75%,#8c6b4d 100%)}
.hero-shade{position:absolute;inset:0;background:linear-gradient(90deg,rgba(20,15,10,.55) 0%,rgba(20,15,10,.1) 55%,rgba(0,0,0,0) 100%)}
.hero-copy{left:100px;top:200px;color:var(--white)}
.hero-copy .eyebrow{font-family:"Roboto Condensed",sans-serif;font-size:40px;font-weight:400;text-transform:uppercase;letter-spacing:1px}
.hero-copy h1{font-family:"Roboto Condensed",sans-serif;font-size:54px;font-weight:700;text-transform:uppercase;line-height:56px}
.hero-copy p{width:420px;margin-top:14px;font-size:14px;line-height:20px;color:#f1ece6}
.hero-arrow{top:300px;width:36px;height:36px;border-radius:50%;background:rgba(255,255,255,.25)}
.hero-curve{left:0;bottom:0}

/* how it works */
.how-it-works{left:0;top:690px;width:1200px}
.steps{left:100px;top:800px;width:1000px;display:flex;justify-content:space-between}
.step{display:flex;gap:16px;width:300px}
.step-icon{flex:none;width:64px;height:64px;border-radius:50%;display:flex;align-items:center;justify-content:center}
.step-icon.blue{background:var(--blue)}
.step-icon.orange{background:var(--orange)}
.step-icon.green{background:var(--green)}
.step h3{font-size:17px;font-weight:500;color:var(--ink);margin:8px 0 6px}
.divider{left:0;top:950px;width:1200px;height:1px;background:var(--line)}

/* services */
.services{left:0;top:975px;width:1200px}
.service-cards{left:100px;top:1040px;width:1000px;display:flex;justify-content:space-between}
.service-card{width:310px}
.service-photo{height:170px}
.service-card h3{font-size:17px;font-weight:500;color:var(--ink);margin:20px 0 8px}
.learn-more{display:inline-block;margin-top:12px;font-size:13px;color:var(--ink);font-weight:500}
.learn-more::after{content:" \203A";color:var(--blue)}

/* tutor profile */
.tutor-profile{left:0;top:1390px;width:1200px;height:430px;background:linear-gradient(120deg,var(--blue-band) 0%,#3aa5e6 50%,var(--blue-band) 100%)}
.tutor-photo{left:160px;top:70px;width:270px;height:270px;border-radius:50%;border:8px solid var(--white);background:radial-gradient(circle at 50% 40%,#e9e3da 0%,#b9c3cc 60%,#8a9aa8 100%)}
.tutor-info{left:470px;top:100px;width:630px;color:var(--white)}
.tutor-info h2{font-family:"Roboto Condensed",sans-serif;font-size:32px;font-weight:400;text-transform:uppercase;letter-spacing:1px}
.tutor-info h2::after{content:"";display:block;width:50px;height:2px;background:var(--white);margin:12px 0 18px}
.tutor-info p{color:#e8f4fc}
.contact-row{display:flex;align-items:center;gap:12px;margin-top:14px;font-size:13px}
.contact-row svg{flex:none}

/* schedule + video */
.schedule-title,.video-title{top:1870px;font-family:"Roboto Condensed",sans-serif;font-size:24px;color:var(--ink);text-transform:uppercase}
.schedule-title{left:100px}
.video-title{left:692px}
.schedule-title::after,.video-title::after{content:"";display:block;width:40px;height:2px;background:var(--blue);margin-top:10px}
.calendar{left:100px;top:1930px;width:285px;border:1px solid var(--line);font-size:12px}
.cal-head{background:var(--blue);color:var(--white);display:flex;justify-content:space-between;padding:8px 12px;font-weight:500}
.cal-grid{display:grid;grid-template-columns:repeat(7,1fr);text-align:center;padding:6px 8px 10px;row-gap:4px;color:var(--ink)}
.cal-grid .dow{color:var(--muted);font-weight:500;padding:4px 0}
.cal-grid span{padding:4px 0}
.cal-grid .dim{color:#c5c9cd}
.cal-grid .today{background:var(--orange);color:var(--white);border-radius:50%;width:24px;height:24px;margin:0 auto;line-height:16px}
.book-btn{left:100px;top:2160px;background:var(--orange);color:var(--white);font-size:12px;padding:6px 14px}
.sessions{left:400px;top:1925px;width:260px}
.session{display:flex;gap:14px;margin-bottom:22px}
.session-avatar{flex:none;width:52px;height:52px;border-radius:50%;background:linear-gradient(135deg,#c9b9a6,#7d8a96)}
.session h4{font-size:14px;font-weight:500;color:var(--ink);margin:4px 0 2px}
.session p{font-size:12px;line-height:17px}
.video{left:692px;top:1930px;width:408px;height:300px;background:#222}
.video-frame{position:absolute;left:0;top:0;width:408px;height:268px;background:linear-gradient(180deg,#3d5a3f 0%,#2c4230 45%,#cfd3d6 46%,#e6e8ea 100%)}
.video-play{position:absolute;left:174px;top:104px}
.video-bar{position:absolute;left:0;bottom:0;width:408px;height:32px;background:#1c1c1c;display:flex;align-items:center;gap:10px;padding:0 10px}
.video-track{flex:1;height:4px;background:#555;position:relative}
.video-track::before{content:"";position:absolute;left:0;top:0;width:35%;height:4px;background:var(--blue)}

/* online training */
.online-training{left:0;top:2270px;width:1200px;height:330px;background:linear-gradient(180deg,#243022 0%,var(--training) 50%,#3e5a35 100%)}
.training-copy{left:200px;top:50px;width:800px;text-align:center;color:var(--white)}
.training-copy h2{font-family:"Roboto Condensed",sans-serif;font-size:38px;font-weight:400;text-transform:uppercase;letter-spacing:1px}
.training-copy p{margin:14px auto 0;width:760px;color:#e2e8e0}
.training-btn{display:inline-block;margin-top:24px;background:var(--blue);color:var(--white);font-size:13px;font-weight:500;padding:10px 26px;text-transform:uppercase}

/* footer */
.site-footer{left:0;top:2600px;width:1200px;height:280px;background:var(--footer);color:var(--white)}
.footer-cols{left:100px;top:40px;width:1000px;display:flex;justify-content:space-between}
.footer-col h4{font-size:16px;font-weight:500;text-transform:uppercase;margin-bottom:18px}
.footer-col p,.footer-col li{font-size:12px;line-height:20px;color:#e3f1fb}
.footer-col ul{list-style:none}
.footer-col li::before{content:"\203A  ";}
.footer-contact{width:230px}
.footer-links{width:150px}
.footer-news{width:290px}
.footer-social{width:150px}
.news-input{margin-top:14px;height:34px;background:var(--white);color:var(--muted);font-size:12px;line-height:34px;padding:0 10px;width:270px}
.news-btn{margin-top:10px;display:inline-block;background:var(--bottom);color:var(--white);font-size:12px;padding:8px 16px;text-transform:uppercase}
.social-item{display:flex;align-items:center;gap:10px;font-size:12px;margin-bottom:10px}
.social-dot{width:24px;height:24px;border-radius:50%;background:rgba(255,255,255,.25)}
.copyright{left:0;top:2880px;width:1200px;height:60px;background:var(--bottom);color:#aab0b5;font-size:12px;text-align:center;line-height:60px}
</style>
</head>
<body>

<header class="site-header abs">
  <div class="brand abs">Brivora</div>
  <nav class="main-nav abs">
    <a class="active">Home</a><a>About Us</a><a>Scheduler</a><a>Administration</a><a>Careers</a><a>Contact Us</a>
  </nav>
</header>

<section class="hero abs">
  <div class="hero-photo" role="img" aria-label="Student holding a tablet in a library with bookshelves behind"></div>
  <div class="hero-shade"></div>
  <div class="hero-arrow abs" style="left:20px"></div>
  <div class="hero-arrow abs" style="right:20px"></div>
  <div class="hero-copy abs">
    <div class="eyebrow">Brivora</div>
    <h1>Online Tutoring</h1>
    <p>Live one-to-one lessons with top university tutors, booked by the hour with no monthly plans.</p>
  </div>
  <svg class="hero-curve abs" width="1200" height="130" viewBox="0 0 1200 130">
    <path d="M0 130 L0 80 C300 140 800 80 1200 0 L1200 130 Z" fill="#ffffff"/>
    <path d="M0 80 C300 140 800 80 1200 0" fill="none" stroke="#1f8fd6" stroke-width="3"/>
  </svg>
</section>

<section class="how-it-works abs"><h2 class="section-title">How It Works</h2></section>
<div class="steps abs">
  <div class="step">
    <div class="step-icon blue"><svg width="28" height="28" viewBox="0 0 28 28"><path d="M6 14l5 5 11-11" fill="none" stroke="#fff" stroke-width="3"/></svg></div>
    <div><h3>Tutor Registration</h3><p class="small">Sign up, build your profile and pass our interview to start teaching.</p></div>
  </div>
  <div class="step">
    <div class="step-icon orange"><svg width="28" height="28" viewBox="0 0 28 28"><circle cx="14" cy="9" r="5" fill="#fff"/><path d="M4 26c0-6 4-9 10-9s10 3 10 9z" fill="#fff"/></svg></div>
    <div><h3>Parent Registration</h3><p class="small">Search tutors and book a free 15 minute video chat first.</p></div>
  </div>
  <div class="step">
    <div class="step-icon green"><svg width="28" height="28" viewBox="0 0 28 28"><rect x="6" y="12" width="16" height="12" rx="2" fill="#fff"/><path d="M9 12V8a5 5 0 0110 0v4" fill="none" stroke="#fff" stroke-width="2.5"/></svg></div>
    <div><h3>Student Log-ins</h3><p class="small">Join your lesson in the live interactive classroom space.</p></div>
  </div>
</div>
<div class="divider abs"></div>

<section class="services abs"><h2 class="section-title">Our Services</h2></section>
<div class="service-cards abs">
  <article class="service-card">
    <div class="service-photo" role="img" aria-label="Student learning on a laptop over a live webcam lesson" style="background:linear-gradient(135deg,#c9a888,#8c6a52 60%,#5a4a40)"></div>
    <h3>Conducted Via Live Webcam</h3>
    <p class="small">Lessons run in real time over webcam inside a dedicated space with a shared whiteboard, chat and file tools.</p>
    <span class="learn-more">Learn More</span>
  </article>
  <article class="service-card">
    <div class="service-photo" role="img" aria-label="University tutor helping a young student with homework" style="background:linear-gradient(135deg,#e8a6a0,#d97a6c 50%,#a5b8c8)"></div>
    <h3>High Scoring Undergraduates</h3>
    <p class="small">Every tutor is a high achieving student from a leading Australian university, ready to guide years 2 to 12.</p>
    <span class="learn-more">Learn More</span>
  </article>
  <article class="service-card">
    <div class="service-photo" role="img" aria-label="Tutor working through an assessment with students at a table" style="background:linear-gradient(135deg,#d8c0a5,#a07a5c 55%,#6d7f8c)"></div>
    <h3>Interviews &amp; Assessments</h3>
    <p class="small">Only top applicants pass our interviews and subject assessments, so each child learns from proven tutors.</p>
    <span class="learn-more">Learn More</span>
  </article>
</div>

<section class="tutor-profile abs">
  <div class="tutor-photo abs" role="img" aria-label="Portrait of a tutor with a student"></div>
  <div class="tutor-info abs">
    <h2>Tutor Profile</h2>
    <p class="small">Each tutor has a full profile showing subjects, university, scores, reviews and weekly availability. Parents can compare tutors, watch a short introduction and message them before booking. Lessons are paid by the hour with no monthly subscription and no limits, so families only pay for the time they use.</p>
    <div class="contact-row"><svg width="18" height="18" viewBox="0 0 18 18"><path d="M4 2l3 3-2 2c1 2 2 3 4 4l2-2 3 3-2 3C7 15 3 11 2 4z" fill="#fff"/></svg>Phone : +61 7 3000 4821</div>
    <div class="contact-row"><svg width="18" height="18" viewBox="0 0 18 18"><rect x="1" y="4" width="16" height="11" fill="none" stroke="#fff" stroke-width="1.5"/><path d="M1 4l8 6 8-6" fill="none" stroke="#fff" stroke-width="1.5"/></svg>info@brivora.com.au</div>
  </div>
</section>

<h3 class="schedule-title abs">Scheduled</h3>
<h3 class="video-title abs">How It Works Video</h3>

<div class="calendar abs">
  <div class="cal-head"><span>&#8249;</span><span>November 2016</span><span>&#8250;</span></div>
  <div class="cal-grid">
    <span class="dow">Su</span><span class="dow">Mo</span><span class="dow">Tu</span><span class="dow">We</span><span class="dow">Th</span><span class="dow">Fr</span><span class="dow">Sa</span>
    <span class="dim">30</span><span class="dim">31</span><span>1</span><span>2</span><span>3</span><span>4</span><span>5</span>
    <span>6</span><span>7</span><span>8</span><span>9</span><span>10</span><span>11</span><span>12</span>
    <span>13</span><span>14</span><span>15</span><span class="today">16</span><span>17</span><span>18</span><span>19</span>
    <span>20</span><span>21</span><span>22</span><span>23</span><span>24</span><span>25</span><span>26</span>
    <span>27</span><span>28</span><span>29</span><span>30</span><span class="dim">1</span><span class="dim">2</span><span class="dim">3</span>
  </div>
</div>
<div class="book-btn abs">Book Now</div>

<div class="sessions abs">
  <div class="session"><div class="session-avatar" role="img" aria-label="Tutor portrait"></div><div><h4>John Doe</h4><p>Year 8 Maths lesson, 4:00 pm to 5:00 pm today</p></div></div>
  <div class="session"><div class="session-avatar" role="img" aria-label="Tutor portrait"></div><div><h4>John Doe</h4><p>Year 5 English lesson, 5:00 pm to 6:00 pm today</p></div></div>
  <div class="session"><div class="session-avatar" role="img" aria-label="Tutor portrait"></div><div><h4>John Doe</h4><p>Year 11 Physics lesson, 6:00 pm to 7:00 pm today</p></div></div>
</div>

<div class="video abs">
  <div class="video-frame" role="img" aria-label="Video still of a teacher and students in front of a chalkboard"></div>
  <svg class="video-play" width="60" height="60" viewBox="0 0 60 60"><circle cx="30" cy="30" r="28" fill="rgba(0,0,0,.55)"/><path d="M24 18l18 12-18 12z" fill="#fff"/></svg>
  <div class="video-bar">
    <svg width="12" height="12" viewBox="0 0 12 12"><path d="M2 1l9 5-9 5z" fill="#fff"/></svg>
    <div class="video-track"></div>
    <span style="color:#ccc;font-size:11px">01:24</span>
  </div>
</div>

<section class="online-training abs" role="img" aria-label="Students studying outdoors on grass, darkened">
  <div class="training-copy abs">
    <h2>Online Training</h2>
    <p class="small">Free training sessions help new tutors learn the interactive classroom, lesson planning and how to keep younger students engaged. Sessions run online every month and are open to all approved tutors.</p>
    <span class="training-btn">Tutor Registration</span>
  </div>
</section>

<footer class="site-footer abs">
  <div class="footer-cols abs">
    <div class="footer-col footer-contact">
      <h4>Contact Us</h4>
      <p>Level 2, 18 Harlow Street, Brisbane<br>QLD 4000, Australia</p>
      <p style="margin-top:10px">Phone : +61 7 3000 4821</p>
      <p>Fax : +61 7 3000 4822</p>
      <p style="margin-top:10px">Email : info@brivora.com.au</p>
    </div>
    <div class="footer-col footer-links">
      <h4>Useful Links</h4>
      <ul><li>Home</li><li>About Us</li><li>Scheduler</li><li>Administration</li><li>Careers</li><li>Contact Us</li></ul>
    </div>
    <div class="footer-col footer-news">
      <h4>Join Our Newsletter</h4>
      <p>Get tutoring tips, new tutor alerts and special offers sent to your inbox each month.</p>
      <div class="news-input">Enter Name</div>
      <div class="news-btn">Subscribe</div>
    </div>
    <div class="footer-col footer-social">
      <h4>Social</h4>
      <div class="social-item"><span class="social-dot"></span>Community</div>
      <div class="social-item"><span class="social-dot"></span>Updates</div>
      <div class="social-item"><span class="social-dot"></span>Forum</div>
      <div class="social-item"><span class="social-dot"></span>Videos</div>
    </div>
  </div>
</footer>
<div class="copyright abs">Copyright 2016 | All Rights Reserved | Brivora</div>

</body>
</html>
```